Marta's Dwellings website

We need a simple website for our property investment business in the UK. We basically need our contact details and brief description.We have the company logo already done (via ArtFlockly) so please use these:https://drive.google.com/drive/folders/1szJ3iRhelElZ40NIFT7w-c14MaY3Y_oV?usp=sharingYou could use some stock photos of UK houses for now.Let me know when to provide more detailed descriptions, etc

Coding

Coded - Design and coding required

Number of Pages Required

1 page

Colors

Designer to choose colors to be used in the design.

```html
<!DOCTYPE html>
<html lang="en">
<head>
<meta charset="utf-8">
<title>Marta's Dwellings</title>
<link href="https://fonts.googleapis.com/css2?family=Montserrat:wght@600;700;800&family=Questrial&display=swap" rel="stylesheet">
<style>
:root{
  --red:#e10a1c;
  --dark:#1c1c1d;
  --blue:#2c4a85;
  --ink:#141414;
  --text:#5a5a5a;
  --light:#f2f2f4;
  --white:#ffffff;
  --star:#f5b800;
}
*{margin:0;padding:0;box-sizing:border-box}
html,body{width:1200px;height:2854px;overflow:hidden}
body{position:relative;background:var(--white);font-family:"Questrial",sans-serif;color:var(--text)}
.abs{position:absolute}
.backdrop{position:absolute;left:0;top:0}
.front{z-index:5}

/* header */
.brand{left:144px;top:18px;width:162px;display:flex;flex-direction:column;align-items:center;gap:10px;color:var(--white)}
.brand-mark{width:30px;height:30px;border:3px solid var(--white)}
.brand-name{font-size:13px;letter-spacing:4px;text-transform:uppercase;white-space:nowrap}
.top-address{left:540px;top:19px;display:flex;gap:12px;align-items:center;color:var(--white);font-size:14px;line-height:18px}
.nav{left:495px;top:76px;height:35px;display:flex;align-items:center;gap:40px}
.nav a{color:var(--white);text-decoration:none;font-family:"Montserrat",sans-serif;font-weight:700;font-size:14px}

/* hero */
.hero-photo{left:0;top:113px;width:1200px;height:613px;background:linear-gradient(180deg,#8c97a5 0%,#9b8b7a 22%,#6d4b3a 55%,#4a3027 100%)}
.hero-title{left:0;top:338px;width:1200px;text-align:center;color:var(--white);font-size:26px;letter-spacing:14px;text-transform:uppercase}
.hero-tagline{left:0;top:384px;width:1200px;text-align:center;color:var(--white);font-family:"Montserrat",sans-serif;font-weight:700;font-size:20px}
.btn{display:inline-flex;align-items:center;gap:8px;background:var(--ink);color:var(--white);border-radius:30px;font-family:"Montserrat",sans-serif;font-weight:700;font-size:14px;text-decoration:none;justify-content:center}
.hero-btn{left:513px;top:448px;width:174px;height:51px}
.circle-arrow{width:28px;height:28px;border-radius:50%;background:rgba(0,0,0,.55);display:flex;align-items:center;justify-content:center}
.dots{left:556px;top:609px;display:flex;gap:8px}
.dots span{width:11px;height:11px;border-radius:50%;background:var(--white)}
.dots span.on{background:transparent;border:2px solid var(--white)}

/* about */
.about-bg{left:0;top:726px;width:1200px;height:600px;background:linear-gradient(90deg,#e9e9ed 0%,#f7f7f9 45%,#ededf0 100%)}
.about-heading{left:143px;top:780px;color:var(--ink);font-size:37px;line-height:46px}
.about-heading b{font-family:"Montserrat",sans-serif;font-weight:700}
.rule{width:46px;height:3px;background:var(--red)}
.about-rule{left:143px;top:884px}
.about-copy{left:143px;top:911px;width:450px;font-size:14.5px;line-height:29px}
.about-btn{left:143px;top:1142px;width:146px;height:48px}
.about-photo{left:655px;top:795px;width:400px;height:390px;background:linear-gradient(160deg,#7e9ccc 0%,#a2553f 40%,#7d3a2b 75%,#c9c2b8 100%);clip-path:polygon(50% 0,100% 32%,100% 100%,0 100%,0 32%)}
.about-word{left:1082px;top:1140px;transform-origin:left top;transform:rotate(-90deg);font-family:"Montserrat",sans-serif;font-weight:800;font-size:118px;color:#e2e2e6;letter-spacing:2px}

/* properties */
.props-bg{left:0;top:1258px;width:1200px;height:572px;background:linear-gradient(90deg,var(--blue) 0%,var(--blue) 55%,#5a5656 80%,#8a5a48 100%);clip-path:polygon(0 0,50% 62px,100% 0,100% 100%,0 100%)}
.props-word{left:-30px;top:1410px;font-family:"Montserrat",sans-serif;font-weight:800;font-size:110px;color:rgba(255,255,255,.05)}
.section-title{left:0;width:1200px;text-align:center;font-size:38px}
.section-title b{font-family:"Montserrat",sans-serif;font-weight:700}
.props-title{top:1386px;color:var(--white)}
.props-rule{left:577px;top:1447px}
.hex-card{left:428px;top:1635px;width:344px;text-align:center;color:var(--white)}
.hex-card h3{font-family:"Montserrat",sans-serif;font-weight:700;font-size:21px;margin-bottom:14px}
.hex-card p{font-size:14px;line-height:24px;margin-bottom:14px}
.hex-card .btn{width:140px;height:38px}
.slide-arrow{top:1680px}

/* testimonials */
.testi-bg{left:0;top:1830px;width:1200px;height:610px;background:linear-gradient(180deg,#efeff2 0%,#f6f6f8 60%,#e6e6ea 100%)}
.testi-word{left:822px;top:2040px;font-family:"Montserrat",sans-serif;font-weight:800;font-size:110px;color:#d8d8dc}
.quote-mark{left:388px;top:2058px;font-family:"Montserrat",sans-serif;font-weight:800;font-size:170px;line-height:170px;color:#d6d6da}
.testi-title{top:1986px;color:var(--ink)}
.testi-rule{left:577px;top:2046px}
.avatar{left:550px;top:2099px;width:100px;height:100px;border-radius:50%;background:linear-gradient(180deg,#8a8f96,#4e5660)}
.quote{left:255px;top:2224px;width:690px;text-align:center;font-size:14.5px;line-height:27px}
.author{left:0;top:2318px;width:1200px;text-align:center;font-size:14px}
.author b{font-family:"Montserrat",sans-serif;font-weight:600;color:var(--red);font-size:17px}
.stars{left:548px;top:2355px;display:flex;gap:3px}
.ring-arrow{width:34px;height:34px;border-radius:50%;border:1.5px solid #555;display:flex;align-items:center;justify-content:center;background:var(--white)}

/* footer */
.footer-col{top:2568px;color:var(--white)}
.footer-col h4{font-family:"Montserrat",sans-serif;font-weight:700;font-size:17px;margin-bottom:22px;text-transform:uppercase}
.footer-col ul{list-style:none;font-size:13px;line-height:22px}
.footer-col li::before{content:"»";margin-right:14px}
.contact-row{display:flex;gap:12px;font-size:12.5px;line-height:17px;margin-bottom:22px}
.signup p{font-size:13px;margin-bottom:14px}
.signup .field{width:226px;height:36px;background:var(--white);color:#444;font-size:12px;padding:11px 16px;margin-bottom:9px}
.signup .sub{display:inline-block;background:var(--red);color:var(--white);font-family:"Montserrat",sans-serif;font-weight:700;font-size:13px;padding:10px 13px}
.footer-line{left:145px;top:2785px;width:910px;height:1px;background:#333}
.copyright{left:145px;top:2814px;color:var(--white);font-size:12px}
.socials{left:876px;top:2804px;display:flex;gap:9px}
.socials span{width:38px;height:38px;border-radius:50%;border:2px solid var(--white)}
</style>
</head>
<body>

<svg class="backdrop" width="1200" height="2854" viewBox="0 0 1200 2854" aria-hidden="true">
  <rect x="0" y="0" width="1200" height="113" fill="#1c1c1d"/>
  <polygon points="458,76 1200,76 1200,112 430,112" fill="#e10a1c"/>
  <rect x="0" y="106" width="440" height="6" fill="#e10a1c"/>
  <rect x="0" y="2440" width="1200" height="414" fill="#1d1d1e"/>
</svg>

<!-- header -->
<div class="abs brand"><span class="brand-mark"></span><span class="brand-name">Marta's Dwellings</span></div>
<div class="abs top-address">
  <svg width="34" height="34" viewBox="0 0 34 34" aria-hidden="true"><circle cx="17" cy="17" r="15.5" fill="none" stroke="#fff" stroke-width="1.5"/><path d="M17 8a6 6 0 0 0-6 6c0 4.5 6 11 6 11s6-6.5 6-11a6 6 0 0 0-6-6z" fill="none" stroke="#fff" stroke-width="1.5"/><circle cx="17" cy="14" r="2" fill="none" stroke="#fff" stroke-width="1.5"/></svg>
  <span>Address - Unit 7, Harbour Court, 14-16 Willow Street, Ashby Vale,<br>Leicestershire, United Kingdom, LE9 4QT</span>
</div>
<nav class="abs nav"><a href="#">HOME</a><a href="#">ABOUT</a><a href="#">SERVICES</a><a href="#">FEATURES</a><a href="#">CONTACT US</a></nav>

<!-- hero -->
<div class="abs hero-photo" role="img" aria-label="Aerial photo of red-brick UK terraced houses at sunset"></div>
<div class="abs hero-title">Marta's Dwellings</div>
<div class="abs hero-tagline">Lorem ipsum dolor sit ametonsectetur adipiscinsed do eiusmod tempor</div>
<a class="abs btn hero-btn" href="#">READ MORE <svg width="13" height="13" viewBox="0 0 14 14" aria-hidden="true"><circle cx="7" cy="7" r="7" fill="#fff"/><path d="M5.5 4l3 3-3 3" stroke="#141414" stroke-width="2" fill="none"/></svg></a>
<div class="abs circle-arrow" style="left:82px;top:359px"><svg width="12" height="12" viewBox="0 0 12 12" aria-hidden="true"><path d="M8 1L3 6l5 5" stroke="#fff" stroke-width="2" fill="none"/></svg></div>
<div class="abs circle-arrow" style="left:1088px;top:359px"><svg width="12" height="12" viewBox="0 0 12 12" aria-hidden="true"><path d="M4 1l5 5-5 5" stroke="#fff" stroke-width="2" fill="none"/></svg></div>
<div class="abs dots"><span></span><span></span><span class="on"></span><span></span><span></span></div>

<!-- about -->
<div class="abs about-bg" role="img" aria-label="Faded photo of a row of suburban houses"></div>
<svg class="backdrop" width="1200" height="800" viewBox="0 0 1200 800" style="top:650px" aria-hidden="true">
  <polygon points="0,76 0,54 600,12 1200,52 1200,76" fill="#fff"/>
  <polygon points="150,46 600,12 1050,46 600,22" fill="#e10a1c"/>
</svg>
<div class="abs about-heading"><b>Welcome to</b><br>Marta's Dwellings</div>
<div class="abs rule about-rule"></div>
<p class="abs about-copy">Lorem ipsum dolor sit amet, consectetur adipiscing elit, sed do eiusmod tempor incididunt ut labore et dolore magna aliqua. Ut enim ad minim veniam, quis nostrud exercitation ullamco laboris nisi ut aliquip ex ea commodo consequat. Duis aute irure dolor in reprehenderit in voluptate velit esse cillum dolore eu fugiat nulla pariatur. Excepteur sint occaecat cupidatat non proident, sunt in culpa qui officia deserunt mollit anim id est laborum</p>
<a class="abs btn about-btn" href="#">READ MORE <svg width="13" height="13" viewBox="0 0 14 14" aria-hidden="true"><circle cx="7" cy="7" r="7" fill="#fff"/><path d="M5.5 4l3 3-3 3" stroke="#141414" stroke-width="2" fill="none"/></svg></a>
<div class="abs about-photo" role="img" aria-label="Photo of a red-brick detached house"></div>
<div class="abs about-word">ABOUT</div>

<!-- properties -->
<div class="abs props-bg" role="img" aria-label="Blue-tinted photo of a house roof and brick wall"></div>
<svg class="backdrop" width="1200" height="700" viewBox="0 0 1200 700" style="top:1140px" aria-hidden="true">
  <polygon points="998,140 1200,8 1200,118" fill="#e10a1c"/>
</svg>
<div class="abs props-word">PERTIES</div>
<div class="abs section-title props-title"><b>Our</b> Properties</div>
<div class="abs rule props-rule"></div>

<!-- testimonials background (drawn before hexagons so they overlap it) -->
<div class="abs testi-bg" role="img" aria-label="Faded photo of a suburban house front"></div>
<svg class="backdrop" width="1200" height="300" viewBox="0 0 1200 300" style="top:1820px" aria-hidden="true">
  <polygon points="0,10 175,0 0,105" fill="#e10a1c"/>
</svg>

<svg class="backdrop front" width="1200" height="460" viewBox="0 0 1200 460" style="top:1495px" aria-hidden="true">
  <polygon points="296,60 446,146 446,320 296,406 146,320 146,146" fill="#fff"/>
  <polygon points="296,84 425,158 425,308 296,382 167,308 167,158" fill="#b3553f"/>
  <polygon points="904,60 1054,146 1054,320 904,406 754,320 754,146" fill="#fff"/>
  <polygon points="904,84 1033,158 1033,308 904,382 775,308 775,158" fill="#d8d3c4"/>
  <polygon points="600,8 787,116 787,334 600,442 413,334 413,116" fill="#fff"/>
  <polygon points="600,32 766,128 766,322 600,418 434,322 434,128" fill="#e3202f"/>
</svg>
<div class="abs front" role="img" aria-label="Photo of a red-brick house" style="left:167px;top:1579px;width:258px;height:298px"></div>
<div class="abs front" role="img" aria-label="Photo of a cream apartment building" style="left:775px;top:1579px;width:258px;height:298px"></div>
<div class="abs hex-card front">
  <h3>Lorem ipsum dolortetu</h3>
  <p>Sed ut perspiciatis unde omnis iste natus<br>error sit voluptatem accusantium<br>doloremquelaudantium</p>
  <a class="btn" href="#">READ MORE <svg width="13" height="13" viewBox="0 0 14 14" aria-hidden="true"><circle cx="7" cy="7" r="7" fill="#fff"/><path d="M5.5 4l3 3-3 3" stroke="#141414" stroke-width="2" fill="none"/></svg></a>
</div>
<svg class="abs slide-arrow" style="left:62px" width="36" height="70" viewBox="0 0 36 70" aria-hidden="true"><path d="M33 2L3 35l30 33" stroke="#fff" stroke-width="1.5" fill="none"/></svg>
<svg class="abs slide-arrow" style="left:1102px" width="36" height="70" viewBox="0 0 36 70" aria-hidden="true"><path d="M3 2l30 33-30 33" stroke="#fff" stroke-width="1.5" fill="none"/></svg>

<!-- testimonials -->
<div class="abs testi-word">TESTIM</div>
<div class="abs quote-mark">“</div>
<div class="abs section-title testi-title"><b>What</b> Clients say</div>
<div class="abs rule testi-rule"></div>
<div class="abs avatar" role="img" aria-label="Portrait photo of the customer"></div>
<div class="abs ring-arrow" style="left:193px;top:2232px"><svg width="10" height="10" viewBox="0 0 10 10" aria-hidden="true"><path d="M7 1L3 5l4 4" stroke="#333" stroke-width="1.6" fill="none"/></svg></div>
<div class="abs ring-arrow" style="left:973px;top:2232px"><svg width="10" height="10" viewBox="0 0 10 10" aria-hidden="true"><path d="M3 1l4 4-4 4" stroke="#333" stroke-width="1.6" fill="none"/></svg></div>
<p class="abs quote">"Lorem ipsum dolor sit amet, consectetur adipiscing elit, sed do eiusmod tempor incididunt ut labore et dolore magna aliquaim ad minim veniam, quis nostrud exercitation ullamco laboris nisi ut aliquip ex ea commodo consequatuis aute irure dolor in reprehenderit in voluptate "</p>
<div class="abs author"><b>- Sam Rowley</b>,Customer</div>
<div class="abs stars">
  <svg width="104" height="20" viewBox="0 0 104 20" aria-hidden="true">
    <g fill="#f5b800">
      <polygon points="10,1 12.6,7 19,7.6 14.2,11.8 15.6,18.5 10,15 4.4,18.5 5.8,11.8 1,7.6 7.4,7"/>
      <polygon transform="translate(21 0)" points="10,1 12.6,7 19,7.6 14.2,11.8 15.6,18.5 10,15 4.4,18.5 5.8,11.8 1,7.6 7.4,7"/>
      <polygon transform="translate(42 0)" points="10,1 12.6,7 19,7.6 14.2,11.8 15.6,18.5 10,15 4.4,18.5 5.8,11.8 1,7.6 7.4,7"/>
      <polygon transform="translate(63 0)" points="10,1 12.6,7 19,7.6 14.2,11.8 15.6,18.5 10,15 4.4,18.5 5.8,11.8 1,7.6 7.4,7"/>
      <polygon transform="translate(84 0)" points="10,1 12.6,7 19,7.6 14.2,11.8 15.6,18.5 10,15 4.4,18.5 5.8,11.8 1,7.6 7.4,7"/>
    </g>
  </svg>
</div>

<!-- footer -->
<svg class="backdrop" width="1200" height="120" viewBox="0 0 1200 120" style="top:2430px" aria-hidden="true">
  <polygon points="0,0 1200,0 1200,12 600,74 0,12" fill="#e7e7eb"/>
  <polygon points="250,36 600,74 950,36 600,64" fill="#e10a1c"/>
</svg>
<div class="abs footer-col" style="left:163px">
  <h4>Contact Info</h4>
  <div class="contact-row">
    <svg width="16" height="20" viewBox="0 0 16 20" aria-hidden="true"><path d="M8 1a6.5 6.5 0 0 0-6.5 6.5C1.5 12.5 8 19 8 19s6.5-6.5 6.5-11.5A6.5 6.5 0 0 0 8 1z" fill="none" stroke="#fff" stroke-width="1.3"/><circle cx="8" cy="7.5" r="2.3" fill="none" stroke="#fff" stroke-width="1.3"/></svg>
    <span>Address - Unit 7, Harbour Court,<br>14-16 Willow Street, Ashby Vale,<br>Leicestershire<br>United Kingdom, LE9 4QT</span>
  </div>
  <div class="contact-row">
    <svg width="18" height="18" viewBox="0 0 18 18" aria-hidden="true"><path d="M4 1.5l3 3.5-1.8 2a10 10 0 0 0 5.8 5.8l2-1.8 3.5 3-1.8 2.3C8 16 2 10 1.7 3.3z" fill="none" stroke="#fff" stroke-width="1.2"/></svg>
    <span>Phone :&nbsp; 1 555 010 2040</span>
  </div>
</div>
<div class="abs footer-col" style="left:433px">
  <h4>Quick Links</h4>
  <ul><li>Home</li><li>About</li><li>Services</li><li>Features</li><li>contact us</li></ul>
</div>
<div class="abs footer-col" style="left:597px">
  <h4>Other Links</h4>
  <ul><li>Terms and conditions</li><li>Sitemap</li><li>Privacy Policy</li><li>Information</li><li>Support</li></ul>
</div>
<div class="abs footer-col signup" style="left:807px">
  <h4>Sign Up Newsletter</h4>
  <p>Lorem ipsum dolor sit amet consectetur</p>
  <div class="field">Enter Email</div>
  <span class="sub">SUBSCRIBE</span>
</div>
<div class="abs footer-line"></div>
<div class="abs copyright">Copyrights © 2019, Marta's Dwellings. All rights reserved</div>
<div class="abs socials"><span></span><span></span><span></span><span></span></div>

</body>
</html>
```